PixelHarbor Rangers (Ledgerline Nova)
A website dedicated to crypto education. We are a new company focused on blockchain edutainment (education and interesting and entertaining content about the blockchain space). We want a fun, clean/minimalist and modern website that is made up of an education platform which could be a website in it’s own right. It will be the reference point for our users/community for all of our other blockchain based content in the PHR website ecosystem which will be covering; crypto news, digital asset investing (including a technical and fundamental analysis subscription service), blockchain business solutions and an NFT section that will cover creative art projects (art, music, gaming and more). To feature a logins and payment system which may need a shopping basket set up for tutorial/educational platform that is accessed via the website, NFT page with sub-categories: education and NFT and metaverse/virtual world and merchandise shopping page which is Web 3.0 enabled (able to link to a VeloPurse, Kindle Vault etc , digital asset education page featuring blog and newsletter subscriptions links, A social media page where people can access videos, podcasts and our presence on other platforms such as Chirplo, Snapmora, Huddlex, Wirepost etc.
Number of Pages Required
5+ page
Look and feel

```html
<!DOCTYPE html>
<html lang="en">
<head>
<meta charset="utf-8">
<title>PixelHarbor Rangers — Crypto Education</title>
<link href="https://fonts.googleapis.com/css2?family=Share+Tech+Mono&family=Nunito:wght@400;600;700;800&display=swap" rel="stylesheet">
<style>
:root{
  --bg:#000;
  --panel:#1a1a1a;
  --card:#222226;
  --purple:#7a2fd4;
  --purple-2:#9b3ee6;
  --violet-text:#8a3fd8;
  --white:#fff;
  --muted:#cfcfcf;
  --blue:#3b8af0;
  --green:#55e05a;
  --line:#2c2c2c;
}
*{margin:0;padding:0;box-sizing:border-box}
html,body{width:1200px;height:5137px;overflow:hidden;background:var(--bg);color:var(--white);font-family:'Nunito',sans-serif}
.page{position:relative;width:1200px;height:5137px}
.abs{position:absolute}
.mono{font-family:'Share Tech Mono',monospace}
.section-title{position:absolute;left:0;width:1200px;text-align:center;font-family:'Share Tech Mono',monospace;font-size:36px;letter-spacing:3px;font-weight:400}
.section-title::after{content:"";display:block;width:34px;height:3px;background:#fff;margin:18px auto 0}
.btn{position:absolute;display:flex;align-items:center;justify-content:center;background:linear-gradient(90deg,var(--purple),var(--purple-2));color:#fff;font-weight:800;font-size:14px;border-radius:3px;box-shadow:0 0 0 4px rgba(122,47,212,.35)}
.read-more{position:absolute;font-size:10px;font-weight:800;color:var(--violet-text);border-left:2px solid var(--violet-text);border-right:2px solid var(--violet-text);padding:2px 12px;letter-spacing:.5px}
/* nav */
.logo{left:36px;top:32px;font-family:'Share Tech Mono',monospace;font-size:48px;color:var(--purple-2);letter-spacing:4px}
.nav{left:308px;top:44px;display:flex;gap:30px;font-family:'Share Tech Mono',monospace;font-size:17px;letter-spacing:1px}
.nav .active{color:var(--purple-2);border-bottom:2px solid var(--purple-2);padding-bottom:8px}
.login{left:1024px;top:37px;width:84px;height:34px;border:2px solid #fff;border-radius:3px;display:flex;align-items:center;justify-content:center;font-family:'Share Tech Mono',monospace;font-size:18px}
/* hero */
.hero-title{left:130px;top:195px;font-family:'Share Tech Mono',monospace;font-size:70px;line-height:80px;letter-spacing:4px}
.hero-text{left:132px;top:384px;font-size:19px;line-height:34px;width:400px}
.illus{position:absolute;border-radius:14px}
/* solutions */
.sol{position:absolute;width:300px;text-align:center}
.sol .icon{width:132px;height:132px;margin:0 auto;border-radius:8px}
.sol h3{font-size:21px;font-weight:700;margin-top:38px}
.sol p{font-size:13px;line-height:20px;margin:24px auto 0;width:230px}
/* investing */
.invest{position:absolute;width:452px;height:270px;background:var(--panel)}
.invest h3{position:absolute;left:182px;top:34px;font-size:21px;font-weight:600}
.invest p{position:absolute;left:182px;top:80px;width:230px;font-size:12px;line-height:18px;color:var(--muted)}
/* news */
.news{position:absolute;width:296px;height:400px;background:#fff;border-radius:10px;overflow:hidden;color:#222}
.news .pic{height:200px}
.news h4{margin:26px 28px 0;font-size:15px;font-weight:600;line-height:20px}
.news p{margin:12px 28px 0;font-size:11px;line-height:16px}
/* edu */
.edu{position:absolute;width:292px;height:320px;background:var(--card);border-radius:8px;overflow:hidden}
.edu .pic{height:150px}
.edu .tag{position:absolute;left:36px;top:116px;background:#2b2b2b;padding:6px 12px;font-family:'Share Tech Mono',monospace;font-size:17px;letter-spacing:2px}
.edu h4{position:absolute;left:22px;top:168px;width:230px;font-size:14px;font-weight:600;line-height:20px}
.edu .small{position:absolute;left:22px;top:232px;width:250px;font-size:11px;line-height:14px}
.edu .off{position:absolute;left:22px;top:228px;background:var(--purple);padding:2px 6px;font-size:21px;font-weight:800;border-radius:3px}
.edu .more{position:absolute;left:26px;top:282px;font-size:11px;font-weight:800}
/* features */
.feat{position:absolute;width:260px;text-align:center}
.feat .icon{width:108px;height:108px;margin:0 auto;background:var(--purple);border-radius:6px}
.feat h3{font-size:20px;font-weight:600;margin-top:40px;line-height:26px}
.feat p{font-size:13px;line-height:20px;margin-top:10px}
/* footer */
.footer-nav{left:0;width:1200px;top:4950px;display:flex;justify-content:center;gap:32px;font-family:'Share Tech Mono',monospace;font-size:17px}
.social{display:flex;gap:14px;left:838px;top:4812px}
.social span{width:40px;height:40px;border:2px solid #fff;border-radius:50%;display:flex;align-items:center;justify-content:center;font-size:7px;font-weight:700}
.cards{left:128px;top:5040px;display:flex;gap:6px}
.cards span{width:36px;height:24px;background:#fff;color:#222;border-radius:3px;font-size:8px;font-weight:800;display:flex;align-items:center;justify-content:center}
</style>
</head>
<body>
<div class="page">

<!-- header -->
<div class="abs logo">PHR</div>
<nav class="abs nav">
  <span class="active">HOME</span><span>ABOUT US</span><span>SOLUTIONS</span><span>NFT</span><span>MERCHANDISE</span><span>BLOG</span><span>CONTACT</span>
</nav>
<div class="abs login">LOGIN</div>
<svg class="abs" style="left:1128px;top:34px" width="40" height="38" viewBox="0 0 40 38" fill="none" stroke="#fff" stroke-width="2.5"><path d="M2 4h6l5 20h20l4-14H11"/><circle cx="15" cy="32" r="3"/><circle cx="30" cy="32" r="3"/></svg>

<!-- hero -->
<h1 class="abs hero-title" style="font-weight:400">CRYPTO<br>EDUCATION</h1>
<p class="abs hero-text">Lorem Ipsum is simply dummy text of the printing and typesetting industry</p>
<div class="btn" style="left:133px;top:490px;width:190px;height:54px">CHECK YOUR RESULT</div>
<div class="illus" role="img" aria-label="Pixel art mascot with red hair, glasses and green shirt" style="left:600px;top:160px;width:470px;height:460px;background:radial-gradient(circle at 55% 45%,#6a4a3a 0,#2a2020 45%,#000 75%)"></div>

<!-- solutions -->
<h2 class="section-title" style="top:730px">SOLUTIONS</h2>
<div class="sol" style="left:105px;top:878px"><div class="icon" role="img" aria-label="Continuous learning icon" style="background:#6a2fd0"></div><h3>Continuous Learning</h3><p>There are many variations of pass ages of Lorem Ipsum available but the majority have.</p></div>
<div class="sol" style="left:450px;top:878px"><div class="icon" role="img" aria-label="Built for beginners icon" style="background:var(--blue)"></div><h3>Built For Beginners</h3><p>There are many variations of pass ages of Lorem Ipsum available but the majority have.</p></div>
<div class="sol" style="left:795px;top:878px"><div class="icon" role="img" aria-label="Analysis icon" style="background:var(--green)"></div><h3>Analysis</h3><p>There are many variations of pass ages of Lorem Ipsum available but the majority have.</p></div>
<div class="read-more" style="left:198px;top:1190px">READ MORE ›</div>
<div class="read-more" style="left:543px;top:1190px;color:var(--blue);border-color:var(--blue)">READ MORE ›</div>
<div class="read-more" style="left:890px;top:1190px;color:var(--green);border-color:var(--green)">READ MORE ›</div>

<!-- digital asset investing -->
<h2 class="section-title" style="top:1316px">DIGITAL ASSET INVESTING</h2>
<div class="invest" style="left:128px;top:1443px">
  <div class="abs" role="img" aria-label="Pixel computer" style="left:40px;top:40px;width:90px;height:90px;background:linear-gradient(#777,#333);border-radius:4px"></div>
  <h3>Technical</h3>
  <p>Sed ut perspiciatis unde omnis iste natus error sit voluptatem accus antium doloremque laudantium, totam rem aperiam, eaque ipsa quae ab illo inventore .</p>
  <div class="read-more" style="left:186px;top:204px">READ MORE ›</div>
</div>
<div class="invest" style="left:616px;top:1443px">
  <div class="abs" role="img" aria-label="Pixel head silhouette" style="left:40px;top:36px;width:90px;height:110px;background:linear-gradient(#fff,#ccc);border-radius:40px 40px 10px 10px"></div>
  <h3>Fundamental analysis</h3>
  <p>Sed ut perspiciatis unde omnis iste natus error sit voluptatem accus antium doloremque laudantium, totam rem aperiam, eaque ipsa quae ab illo inventore .</p>
  <div class="read-more" style="left:186px;top:204px">READ MORE ›</div>
</div>

<!-- crypto news -->
<h2 class="section-title" style="top:1783px">CRYPTO NEWS</h2>
<div class="news" style="left:128px;top:1900px"><div class="pic" role="img" aria-label="Pixel character at a computer desk" style="background:linear-gradient(#2a2226,#3a2a2a)"></div><h4>Sed ut perspiciatis unde omnis iste natus error sit volupt.</h4><p>Sed ut perspiciatis unde omnis iste nat us error sit voluptatem accus.</p><div class="read-more" style="left:28px;top:340px">READ MORE ›</div></div>
<div class="news" style="left:453px;top:1900px"><div class="pic" role="img" aria-label="Pixel ghost on dark background" style="background:linear-gradient(#444,#222)"></div><h4>Sed ut perspiciatis unde omnis iste natus error sit volupt.</h4><p>Sed ut perspiciatis unde omnis iste nat us error sit voluptatem accus.</p><div class="read-more" style="left:28px;top:340px">READ MORE ›</div></div>
<div class="news" style="left:773px;top:1900px"><div class="pic" role="img" aria-label="Hooded pixel figure on a blue pedestal" style="background:linear-gradient(#55557a,#30304a)"></div><h4>Sed ut perspiciatis unde omnis iste natus error sit volupt.</h4><p>Sed ut perspiciatis unde omnis iste nat us error sit voluptatem accus.</p><div class="read-more" style="left:28px;top:340px">READ MORE ›</div></div>

<!-- projects -->
<div class="illus" role="img" aria-label="Blue flame pixel creature" style="left:128px;top:2410px;width:205px;height:208px;background:radial-gradient(circle,#1e4a8a,#161a2a 70%);border-radius:8px"></div>
<div class="illus" role="img" aria-label="Pixel skeleton character" style="left:355px;top:2393px;width:205px;height:197px;background:#1a1a22;border-radius:8px"></div>
<div class="illus" role="img" aria-label="Pixel alien in a space capsule" style="left:128px;top:2637px;width:205px;height:190px;background:radial-gradient(circle,#4a4060,#1a1a24 70%);border-radius:8px"></div>
<div class="illus" role="img" aria-label="Pixel vampire with red cape" style="left:355px;top:2610px;width:205px;height:247px;background:linear-gradient(#8ac8f0,#5aaee8);border-radius:8px"></div>
<h2 class="abs mono" style="left:636px;top:2418px;font-size:34px;font-weight:400;letter-spacing:3px">OUR PROJECTS</h2>
<div class="abs" style="left:638px;top:2478px;width:46px;height:3px;background:#fff"></div>
<p class="abs" style="left:636px;top:2530px;width:440px;font-size:14px;line-height:26px">There are many variations of passages of Lorem Ipsum available, but the majority have suffered alteration in some form, by injected humour, or randomised words which don't look even slightly believable. If you are going to use a passage of Lorem Ipsum, you need to be sure .</p>
<div class="btn" style="left:641px;top:2730px;width:182px;height:52px">VIEW ALL PROJECTS</div>

<!-- digital asset education -->
<h2 class="section-title" style="top:2952px">DIGITAL ASSET EDUCATION</h2>
<div class="edu" style="left:128px;top:3063px"><div class="pic" role="img" aria-label="Pixel soldier facing green aliens" style="background:linear-gradient(#2a2a30,#1e1e22)"></div><div class="tag">PAID</div><h4>Lorem Ipsum is simply dummy text of the printing</h4><div class="off">GER 20% OFF</div><div class="more">READ MORE &nbsp;›</div></div>
<div class="edu" style="left:454px;top:3063px"><div class="pic" role="img" aria-label="Pixel knight in a stone hall" style="background:linear-gradient(#4a4040,#2a2424)"></div><div class="tag">FREE</div><h4>Lorem Ipsum is simply dummy text of the printing</h4><p class="small">There are many variations of passages of Lorem Ipsum available.</p><div class="more">READ MORE &nbsp;›</div></div>
<div class="edu" style="left:775px;top:3063px"><div class="pic" role="img" aria-label="Pixel dragon breathing fire" style="background:linear-gradient(#24304a,#1a2030)"></div><div class="tag">PAID</div><h4>Lorem Ipsum is simply dummy text of the printing</h4><div class="off">GER 50% OFF</div><div class="more">READ MORE &nbsp;›</div></div>
<div class="btn" style="left:515px;top:3428px;width:182px;height:50px">VIEW ALL &nbsp;›</div>

<!-- features -->
<h2 class="section-title" style="top:3563px">FEATURES</h2>
<div class="feat" style="left:90px;top:3690px"><div class="icon" role="img" aria-label="Token icon"></div><h3>Earn Tokens</h3><p>There are many variations<br>of pass ages of Lorem Ipsum<br>available but the majorit.</p></div>
<div class="feat" style="left:342px;top:3690px"><div class="icon" role="img" aria-label="Levels icon"></div><h3>Achieving Levels</h3><p>There are many variations<br>of pass ages of Lorem Ipsum<br>available but the majorit.</p></div>
<div class="feat" style="left:592px;top:3690px"><div class="icon" role="img" aria-label="Community icon"></div><h3>Contributing to<br>the community<br>ecosystem</h3><p style="margin-top:2px">There are many variations<br>of pass ages of Lorem Ipsum</p></div>
<div class="feat" style="left:848px;top:3690px"><div class="icon" role="img" aria-label="Social network icon"></div><h3>Marketing via<br>social media</h3><p>There are many variations<br>of pass ages of Lorem Ipsum<br>available but the majorit.</p></div>

<!-- video -->
<h2 class="section-title" style="top:4040px">OUR VIDEO</h2>
<div class="illus" role="img" aria-label="Pixel art fight scene between two characters" style="left:130px;top:4160px;width:940px;height:385px;background:linear-gradient(#dbe8f4,#c8d8ec 60%,#8a6a4a);border-radius:10px"></div>
<svg class="abs" style="left:558px;top:4320px" width="64" height="64" viewBox="0 0 64 64"><circle cx="32" cy="32" r="30" fill="#8a2fe0"/><path d="M25 19l21 13-21 13z" fill="#fff"/></svg>

<!-- footer -->
<h2 class="abs mono" style="left:130px;top:4780px;font-size:28px;font-weight:400;letter-spacing:2px">NEWSLETTER</h2>
<div class="abs" style="left:128px;top:4838px;width:415px;height:52px;background:#1c1c1c;border-radius:4px"></div>
<svg class="abs" style="left:146px;top:4857px" width="16" height="13" viewBox="0 0 16 13"><rect width="16" height="13" rx="1" fill="#fff"/><path d="M1 1l7 6 7-6" stroke="#1c1c1c" fill="none" stroke-width="1.5"/></svg>
<span class="abs" style="left:176px;top:4855px;font-size:13px">Email id</span>
<div class="btn" style="left:422px;top:4838px;width:121px;height:52px;box-shadow:none;border-radius:4px">SUBSCRIBE</div>
<span class="abs mono" style="left:764px;top:4860px;font-size:18px">FOLLOW</span>
<div class="abs social"><span>Chirplo</span><span>Snapmora</span><span>Huddlex</span><span>Wirepost</span></div>
<div class="abs" style="left:765px;top:4880px;display:flex;align-items:center;gap:10px"><span style="width:22px;height:22px;background:#e2761b;display:inline-block"></span><span class="mono" style="font-size:20px;letter-spacing:3px">VeloPurse</span></div>
<div class="abs" style="left:945px;top:4880px;display:flex;align-items:center;gap:8px"><span style="width:22px;height:22px;border:2px solid var(--blue);border-radius:50%;display:inline-block"></span><span style="font-size:14px;color:var(--blue)">Kindle Vault</span></div>
<div class="abs" style="left:128px;top:4924px;width:942px;height:1px;background:var(--line)"></div>
<div class="abs footer-nav"><span>HOME</span><span>ABOUT US</span><span>SOLUTIONS</span><span>NFT</span><span>MERCHANDISE</span><span>BLOG</span><span>CONTACT</span></div>
<div class="abs cards"><span>Paylo</span><span>Dinero</span><span>Amvex</span><span>Findly</span><span>Duocard</span></div>
<span class="abs" style="left:865px;top:5046px;font-size:11px">Copyright © 2022 All Rights Reserved</span>

</div>
</body>
</html>
```